Website for Briar Hollow Gathering Church

Wordpress website design required for Briar Hollow Gathering Church. We are a family oriented church catering for age groups from school age to elderly people. The church has a wide variety of activities which it coordinates. The idea is to describe the activities on the activities page, but cross-link them to show which would be applicable to the different age groups.

We would like an inviting website which is easy to read and navigate.

Target Market(s)

Very wide audience - from school age youth to elderly people, so design and style should cater for both audiences.

Industry/Entity Type

Church

Coding

Coded - Design and coding required

Number of Pages Required

5+ page

Font styles to use
Sans Serif

Colors
0255a3
ffffff
0792cd
f78f20

Requirements
Must have
• Inviting website.
• Clear readable font.
• Space to import photos to balance text on each page.
• Need to project a dynamic and progressive feel for the church.
• Easy to navigate.
Nice to have
• Scrolling photos on pages. Ability to enter questions/ comments/prayer requests on Home page.
Should not have
• Conservative audience, so should not be too bold.

```html
<!DOCTYPE html>
<html lang="en">
<head>
<meta charset="utf-8">
<title>Briar Hollow Gathering Church</title>
<link rel="stylesheet" href="https://fonts.googleapis.com/css2?family=Roboto:wght@300;400;500;700&family=Roboto+Condensed:wght@400;500&display=swap">
<style>
:root{
  --navy:#0255a3;
  --blue:#0792cd;
  --orange:#f78f20;
  --white:#ffffff;
  --ink:#2b2b2b;
  --grey:#6f6f6f;
  --footer:#2a221c;
  --bar:#161412;
}
*{box-sizing:border-box;margin:0;padding:0}
html,body{width:1200px;height:2922px;overflow:hidden}
body{position:relative;font-family:"Roboto",sans-serif;color:var(--ink);background:var(--white)}
.abs{position:absolute}

/* header */
.site-header{position:absolute;left:0;top:0;width:1200px;height:113px;background:var(--white)}
.nav-link{position:absolute;top:50px;height:34px;line-height:34px;font-size:15px;color:#333;text-transform:uppercase}
.nav-link.active{background:var(--orange);color:var(--white);padding:0 19px}
.brand{position:absolute;left:468px;top:58px;display:flex;align-items:center;gap:8px}
.brand-dot{width:12px;height:12px;border-radius:50%;background:var(--navy)}
.brand-name{font-size:17px;font-weight:500;color:var(--navy)}

/* hero */
.hero{position:absolute;left:0;top:113px;width:1200px;height:544px;
  background:radial-gradient(ellipse at 50% 35%,#a88a6a 0%,#6b4c33 40%,#3a2616 80%,#24160c 100%)}
.hero-title{position:absolute;left:0;width:1200px;top:250px;text-align:center;font-family:"Roboto Condensed",sans-serif;font-size:42px;color:var(--white);font-weight:400}
.hero-sub{position:absolute;left:0;width:1200px;top:303px;text-align:center;font-family:"Roboto Condensed",sans-serif;font-size:23px;color:var(--white)}
.hero-arrow{position:absolute;top:280px;width:42px;height:42px;border-radius:50%;background:rgba(0,0,0,.75)}

/* locations */
.section-title{position:absolute;left:0;width:1200px;text-align:center;font-size:29px;font-weight:400;color:var(--ink);text-transform:uppercase}
.location{position:absolute;top:772px;width:380px;text-align:center}
.location h3{font-size:21px;font-weight:500;color:var(--orange);text-transform:uppercase}
.location p{margin-top:10px;font-size:15px;color:#333}

/* welcome */
.welcome{position:absolute;left:0;top:908px;width:1200px;height:345px;
  background:linear-gradient(180deg,#1784c6 0%,#0d7fc3 50%,#0a6fb0 100%)}
.welcome h2{position:absolute;left:0;top:64px;width:1200px;text-align:center;font-size:29px;font-weight:400;color:var(--white)}
.welcome p{position:absolute;left:97px;top:116px;width:1006px;text-align:center;font-size:15.5px;line-height:26px;color:var(--white)}
.btn-outline{position:absolute;left:534px;top:243px;width:132px;height:41px;border:1px solid var(--white);border-radius:3px;color:var(--white);font-size:15px;text-align:center;line-height:39px}

/* features */
.feature-media{position:absolute;top:1290px;width:500px;height:253px}
.play{position:absolute;left:222px;top:99px;width:56px;height:56px}
.feature-title{position:absolute;top:1570px;width:500px;text-align:center;font-size:22px;font-weight:400;color:var(--ink);text-transform:uppercase}
.feature-text{position:absolute;top:1609px;width:500px;text-align:center;font-size:15.5px;line-height:24px;color:var(--grey);padding:0 10px}
.btn{position:absolute;height:49px;background:var(--blue);color:var(--white);font-size:17px;text-align:center;line-height:49px;text-transform:uppercase;border-radius:2px}

/* prayer */
.prayer{position:absolute;left:0;top:1798px;width:1200px;height:349px;
  background:linear-gradient(180deg,#f39a32 0%,#ee8e25 50%,#e48420 100%)}
.prayer h2{position:absolute;left:0;top:42px;width:1200px;text-align:center;font-size:29px;font-weight:400;color:var(--white)}
.field{position:absolute;background:var(--white);font-size:12px;color:#777;padding:15px 16px;text-transform:uppercase}

/* news */
.news-title span{color:var(--orange)}
.news-card{position:absolute;top:2262px;width:312px}
.news-media{position:relative;height:190px;border:4px solid #eee}
.news-date{position:absolute;left:0;top:44px;width:40px;background:var(--orange);color:var(--white);text-align:center;padding:4px 0}
.news-date b{display:block;font-size:20px;font-weight:500;line-height:22px}
.news-date i{display:block;font-style:normal;font-size:10px}
.news-year{position:absolute;left:0;top:103px;width:40px;height:26px;background:rgba(0,0,0,.55);color:var(--white);font-size:13px;text-align:center;line-height:26px}
.news-card h4{margin-top:18px;font-size:14.5px;font-weight:400;color:#222}
.news-card p{margin-top:12px;font-size:11px;line-height:16px;color:var(--grey)}
.news-card a{display:block;margin-top:14px;font-size:11.5px;color:var(--orange);text-decoration:none}

/* footer */
.site-footer{position:absolute;left:0;top:2620px;width:1200px;height:225px;
  background:linear-gradient(90deg,#2c241e 0%,#3a2c20 50%,#2a221c 100%)}
.foot-col{position:absolute;top:37px;color:var(--white)}
.foot-col h5{font-size:15px;font-weight:500;text-transform:uppercase;margin-bottom:18px}
.foot-col li{list-style:none;font-size:11.5px;line-height:25px}
.foot-col li::before{content:"";display:inline-block;border-left:6px solid var(--white);border-top:4px solid transparent;border-bottom:4px solid transparent;margin-right:8px}
.foot-col p{font-size:11px;line-height:16px}
.subscribe{position:absolute;left:908px;top:107px;display:flex}
.subscribe span{width:148px;height:32px;background:var(--white);color:#888;font-size:11px;line-height:32px;padding-left:10px}
.subscribe b{width:54px;height:32px;background:var(--orange);color:var(--white);font-weight:400;font-size:12px;line-height:32px;text-align:center}
.social{position:absolute;top:157px;width:32px;height:32px;border:1.5px solid var(--white);border-radius:50%}
.bottom-bar{position:absolute;left:0;top:2845px;width:1200px;height:77px;background:var(--bar);color:var(--white);font-size:12px;text-align:center;line-height:62px}
</style>
</head>
<body>

<header class="site-header">
  <a class="nav-link active" style="left:92px">Home</a>
  <a class="nav-link" style="left:203px">Age Group</a>
  <a class="nav-link" style="left:335px">Activites</a>
  <div class="brand"><span class="brand-dot"></span><span class="brand-name">Briar Hollow Gathering Church</span></div>
  <a class="nav-link" style="left:760px">Events Calendar</a>
  <a class="nav-link" style="left:945px">About</a>
  <a class="nav-link" style="left:1038px">Contact</a>
</header>

<section class="hero" role="img" aria-label="Church interior with wooden pews, red aisle carpet and a cross above the altar">
  <h1 class="hero-title">BRIAR HOLLOW GATHERING CHURCH</h1>
  <p class="hero-sub">Neque porro quisquam est qui dolorem ipsum quia</p>
  <span class="hero-arrow" style="left:61px"><svg width="42" height="42"><path d="M24 14l-7 7 7 7" fill="none" stroke="#fff" stroke-width="3"/></svg></span>
  <span class="hero-arrow" style="left:1095px"><svg width="42" height="42"><path d="M18 14l7 7-7 7" fill="none" stroke="#fff" stroke-width="3"/></svg></span>
</section>

<h2 class="section-title" style="top:701px">Locations &amp; Service Times</h2>
<div class="location" style="left:44px"><h3>Cedar Northway</h3><p>Sundays: 9 a.m., 11:15 a.m., 5 p.m., 7:15 p.m.</p></div>
<div class="location" style="left:437px"><h3>Willow Mound | Ferndale</h3><p>Saturdays: 5 p.m., 7:15 p.m. | Sundays: 9 a.m., 11:15 a.m.</p></div>
<div class="location" style="left:808px"><h3>Fort Halden</h3><p>Sundays: 9 a.m., 11:15 a.m., 5 p.m.</p></div>

<section class="welcome" role="img" aria-label="Blue-tinted view of church pews">
  <h2>WELCOME TO BRIAR HOLLOW GATHERING CHURCH</h2>
  <p>For many years our Church has grown through seasons of renewal while keeping the warm, simple spirit of its first building. Fitting for the quiet hillside on which it stands, our Church welcome cards carry the words 'Rooted in Welcome'. Begun as the small Briar Hollow Chapel and later joining the Gathering Church Fellowship, as the Briar Hollow Gathering Church, it has been a place of community worship in Ashford Valley and for spreading the good news of the gospel of Jesus.</p>
  <a class="btn-outline">READ MORE</a>
</section>

<div class="feature-media" style="left:90px;background:linear-gradient(135deg,#c9a56a 0%,#7a4a3a 45%,#3e2a2a 100%)" role="img" aria-label="Video still of a smiling congregation holding bibles">
  <svg class="play" viewBox="0 0 56 56"><circle cx="28" cy="28" r="27" fill="rgba(0,0,0,.55)"/><path d="M22 16l18 12-18 12z" fill="#fff"/></svg>
</div>
<div class="feature-media" style="left:610px;background:linear-gradient(160deg,#d47a2e 0%,#b86a35 30%,#e9e6e0 55%,#7a8f5a 100%)" role="img" aria-label="Video still of a white chapel among autumn trees">
  <svg class="play" viewBox="0 0 56 56"><circle cx="28" cy="28" r="27" fill="rgba(0,0,0,.55)"/><path d="M22 16l18 12-18 12z" fill="#fff"/></svg>
</div>
<h3 class="feature-title" style="left:90px">Family Oriented Church Catering</h3>
<h3 class="feature-title" style="left:610px">Podcast Show</h3>
<p class="feature-text" style="left:90px">Lorem Ipsum has been the industry's standard dummy text ever since the 1500s, when an unknown printer took a galley of type and scrambled it to make a type specimen book.</p>
<p class="feature-text" style="left:610px">Lorem Ipsum has been the industry's standard dummy text ever since the 1500s, when an unknown printer took a galley of type and scrambled it to make a type specimen book.</p>
<a class="btn" style="left:257px;top:1708px;width:164px">View More</a>
<a class="btn" style="left:777px;top:1704px;width:164px">View More</a>

<section class="prayer" role="img" aria-label="Orange-tinted church interior">
  <h2>PRAYER REQUESTS</h2>
  <div class="field" style="left:90px;top:117px;width:489px;height:51px">Name</div>
  <div class="field" style="left:90px;top:181px;width:489px;height:51px">Enter Questions</div>
  <div class="field" style="left:594px;top:117px;width:516px;height:115px">Comments</div>
  <a class="btn" style="left:489px;top:255px;width:222px">Prayer Requests</a>
</section>

<h2 class="section-title news-title" style="top:2191px">Latest <span>News</span></h2>

<article class="news-card" style="left:90px">
  <div class="news-media" role="img" aria-label="Closed bible on a dark table" style="background:linear-gradient(135deg,#c8b8a8 0%,#6a5a50 45%,#222 100%)">
    <div class="news-date"><b>02</b><i>JUN</i></div><div class="news-year">2016</div>
  </div>
  <h4>Neque porro quisquam est qui dolorem</h4>
  <p>Lorem Ipsum has been the industry's standard dummy text ever since the 1500s, when an unknown printer took a galley</p>
  <a>Read More »</a>
</article>
<article class="news-card" style="left:442px">
  <div class="news-media" role="img" aria-label="Cross silhouette against warm blurred lights" style="background:radial-gradient(circle at 55% 45%,#f4c690 0%,#c8623e 45%,#5a1e22 100%)">
    <div class="news-date"><b>02</b><i>JUN</i></div><div class="news-year">2016</div>
  </div>
  <h4>Neque porro quisquam est qui dolorem</h4>
  <p>Lorem Ipsum has been the industry's standard dummy text ever since the 1500s, when an unknown printer took a galley</p>
  <a>Read More »</a>
</article>
<article class="news-card" style="left:795px">
  <div class="news-media" role="img" aria-label="Grand cathedral nave with golden light" style="background:linear-gradient(180deg,#8a6a40 0%,#c9a060 45%,#4a3524 100%)">
    <div class="news-date"><b>02</b><i>JUN</i></div><div class="news-year">2016</div>
  </div>
  <h4>Neque porro quisquam est qui dolorem</h4>
  <p>Lorem Ipsum has been the industry's standard dummy text ever since the 1500s, when an unknown printer took a galley</p>
  <a>Read More »</a>
</article>

<footer class="site-footer">
  <div class="foot-col" style="left:92px">
    <h5>Links</h5>
    <ul><li>Customer Support</li><li>Documentation</li><li>Resources</li><li>General FAQs</li><li>Shortcodes</li></ul>
  </div>
  <div class="foot-col" style="left:302px;width:230px">
    <h5>Church Catering</h5>
    <p>Lorem Ipsum has been the industry's standard dummy text ever since the 1500s, when an unknown printer took</p>
    <p style="margin-top:6px">a galley of type and scrambled it to make a type specimen book. It has survived not only five centuries, but also the leap into electronic typeset-</p>
  </div>
  <div class="foot-col" style="left:653px;width:220px">
    <h5>Get In Touch</h5>
    <p>Address : 1200 Larkspur Ave,<br>Glenmoor, NJ</p>
    <p style="margin-top:16px">Phone : 201 555 0147</p>
    <p style="margin-top:16px">Email : info@briarhollow.example</p>
  </div>
  <div class="foot-col" style="left:908px;width:210px">
    <h5>Newsletter</h5>
    <p>Your about us information would fit<br>here nicely.</p>
  </div>
  <div class="subscribe"><span>Email address</span><b>Submit</b></div>
  <span class="social" style="left:909px"></span>
  <span class="social" style="left:958px"></span>
  <span class="social" style="left:1007px"></span>
</footer>
<div class="bottom-bar">Copyright © 2016. All Rights Reserved</div>

</body>
</html>
```